Business Card For Halvenmoor Financial Consulting

Hi, I would like a business card designed. Bold, modern.
Please use the same design as the logo. I have also attached the website design to see the overall theme.
Wordmark Font
Color: Hex: #01AEF7

```html
<!DOCTYPE html>
<html lang="en">
<head>
<meta charset="utf-8">
<title>Halvenmoor Financial Consulting – Business Card</title>
<link rel="stylesheet" href="https://fonts.googleapis.com/css2?family=Montserrat:wght@300;400;700&display=swap">
<style>
  :root {
    --backdrop: #262729;
    --navy-light: #2f3d4a;
    --navy-dark: #131e28;
    --brand-blue: #2f9fd8;
    --brand-blue-light: #3aa8e0;
    --ink-dark: #17222c;
    --paper-white: #e9ecef;
    --text-soft: #d5dade;
  }
  * { box-sizing: border-box; margin: 0; padding: 0; }
  html, body {
    width: 1200px; height: 960px; overflow: hidden;
    background: var(--backdrop);
    font-family: "Montserrat", Arial, sans-serif;
  }
  .stage {
    width: 1200px; height: 960px;
    display: flex; flex-direction: column; align-items: center; justify-content: center;
    gap: 36px;
  }
  .card {
    position: relative;
    width: 760px; height: 434px;
    overflow: hidden;
    background: radial-gradient(ellipse at 40% 35%, var(--navy-light) 0%, var(--navy-dark) 80%);
    box-shadow: 0 14px 30px rgba(0,0,0,.55);
  }

  /* shared wordmark */
  .wordmark { display: flex; align-items: center; gap: 14px; color: var(--paper-white); font-weight: 700; }
  .wordmark__square { width: 46px; height: 46px; border: 5px solid var(--paper-white); flex: none; }
  .wordmark__text { display: flex; flex-direction: column; line-height: 1; }
  .wordmark__name { font-size: 44px; letter-spacing: 3px; }
  .wordmark__tag { font-size: 13px; letter-spacing: 14.5px; margin-top: 8px; color: var(--brand-blue); }

  /* back */
  .card--back .wordmark { position: absolute; left: 70px; top: 150px; }
  .card--back .wordmark__name { font-size: 50px; }
  .card--back .wordmark__tag { letter-spacing: 17px; font-size: 14px; }
  .edge-bar { position: absolute; height: 8px; background: var(--paper-white); }
  .card--back .edge-bar { left: 24px; right: 230px; bottom: 150px; }
  .corner-band { position: absolute; right: 0; bottom: 0; }

  /* front */
  .name-panel { position: absolute; left: 0; top: 0; }
  .holder { position: absolute; left: 30px; bottom: 96px; }
  .holder__name { font-size: 22px; font-weight: 400; color: var(--ink-dark); letter-spacing: 1px; }
  .holder__title { font-size: 17px; font-weight: 300; color: var(--paper-white); margin-top: 6px; }
  .card--front .wordmark { position: absolute; right: 40px; top: 128px; }
  .card--front .wordmark__name { font-size: 36px; }
  .card--front .wordmark__tag { font-size: 11px; letter-spacing: 12.4px; }
  .card--front .wordmark__square { width: 38px; height: 38px; border-width: 4px; }
  .card--front .edge-bar { left: 256px; right: 34px; bottom: 18px; }

  .contact {
    position: absolute; right: 40px; top: 226px;
    list-style: none; text-align: right;
    color: var(--text-soft); font-weight: 300; font-size: 16px; line-height: 24px;
  }
  .contact__item { display: flex; justify-content: flex-end; align-items: center; gap: 10px; }
  .contact__icon { width: 16px; height: 16px; flex: none; }
  .contact__item--address { padding-right: 26px; }
</style>
</head>
<body>
<main class="stage">

  <section class="card card--back" aria-label="Business card back">
    <div class="wordmark">
      <span class="wordmark__square"></span>
      <span class="wordmark__text">
        <span class="wordmark__name">HALVENMOOR</span>
        <span class="wordmark__tag">CONSULTING</span>
      </span>
    </div>
    <div class="edge-bar"></div>
    <svg class="corner-band" width="330" height="190" viewBox="0 0 330 190" aria-hidden="true">
      <polygon points="140,40 330,0 330,190 30,190" fill="var(--brand-blue)"/>
    </svg>
  </section>

  <section class="card card--front" aria-label="Business card front">
    <svg class="name-panel" width="300" height="434" viewBox="0 0 300 434" aria-hidden="true">
      <defs>
        <linearGradient id="panelFill" x1="0" y1="1" x2="1" y2="0">
          <stop offset="0" stop-color="var(--brand-blue)"/>
          <stop offset="1" stop-color="var(--brand-blue-light)"/>
        </linearGradient>
      </defs>
      <polygon points="0,120 264,0 250,434 0,434" fill="url(#panelFill)"/>
    </svg>
    <div class="holder">
      <p class="holder__name">MARA ELLISON</p>
      <p class="holder__title">Chairmen</p>
    </div>

    <div class="wordmark">
      <span class="wordmark__square"></span>
      <span class="wordmark__text">
        <span class="wordmark__name">HALVENMOOR</span>
        <span class="wordmark__tag">CONSULTING</span>
      </span>
    </div>

    <ul class="contact">
      <li class="contact__item">+1 555 014 2290
        <svg class="contact__icon" viewBox="0 0 16 16" aria-hidden="true"><path d="M4 1l2.5 3-1.5 2a9 9 0 0 0 5 5l2-1.5 3 2.5-1.5 2.5C7 15 1 9 1.5 3.5z" fill="var(--brand-blue)"/></svg>
      </li>
      <li class="contact__item">halvenmoorfinancial@gmail.com
        <svg class="contact__icon" viewBox="0 0 16 16" aria-hidden="true"><rect x="1" y="3" width="14" height="10" fill="var(--brand-blue)"/><path d="M1 3l7 6 7-6" stroke="var(--navy-dark)" stroke-width="1.3" fill="none"/></svg>
      </li>
      <li class="contact__item">www.halvenmoorfinancial.com
        <svg class="contact__icon" viewBox="0 0 16 16" aria-hidden="true"><circle cx="8" cy="8" r="7" fill="var(--brand-blue)"/><path d="M1 8h14M8 1v14M3 4h10M3 12h10" stroke="var(--navy-dark)" stroke-width="1"/><ellipse cx="8" cy="8" rx="3" ry="7" stroke="var(--navy-dark)" stroke-width="1" fill="none"/></svg>
      </li>
      <li class="contact__item contact__item--address">2180 Larkfield Row Apt. 14,</li>
      <li class="contact__item contact__item--address">Port Evanshire</li>
    </ul>

    <div class="edge-bar"></div>
  </section>

</main>
</body>
</html>
```